Meadowlark Scalp Parlour jojoba oil

Hello there!
I am looking to have a label created for a jojoba oil product I am launching. I have attached the logo of my company below. The label should have the following information on it as well:
Ingredients: pure jojoba oil
Size of the bottle: 118ml
And there might be more but I am working on this and will keep you posted.

```html
<!DOCTYPE html>
<html lang="en">
<head>
<meta charset="utf-8">
<title>Meadowlark Scalp Parlour – Jojoba Oil Label</title>
<link rel="stylesheet" href="https://fonts.googleapis.com/css2?family=Oswald:wght@600;700&family=Montserrat:wght@500&family=Roboto:wght@400&display=swap">
<style>
  :root {
    --page: #efe9df;
    --label-black: #1f1d1e;
    --brick: #a5544a;
    --brick-light: #c98a7e;
    --olive: #a8a67b;
    --white: #ffffff;
    --cream-text: #f4ece6;
    --dark-text: #2a2626;
    --gold-light: #f7d77a;
    --gold-deep: #a66d0c;
    --fruit-red: #b5432e;
    --fruit-dark: #6e2414;
  }
  * { box-sizing: border-box; margin: 0; padding: 0; }
  html, body { width: 1200px; height: 795px; overflow: hidden; }
  body { background: var(--page); position: relative; }

  .label {
    position: absolute; left: 336px; top: 41px;
    width: 527px; height: 712px;
    background: var(--label-black);
    overflow: hidden;
  }
  .label__shapes { position: absolute; inset: 0; }

  .brand-plate {
    position: absolute; left: 92px; top: 86px; width: 352px; height: 140px;
    background: var(--white);
    display: flex; flex-direction: column; align-items: center; justify-content: center;
    font-family: "Montserrat", sans-serif; font-weight: 500; color: var(--dark-text);
  }
  .brand-plate__name { font-size: 34px; letter-spacing: 2px; line-height: 1.1; }
  .brand-plate__sub { font-size: 13px; letter-spacing: 7px; margin-top: 6px; }

  .claim {
    position: absolute; left: 86px; top: 285px;
    font-family: "Montserrat", sans-serif; font-weight: 500;
    font-size: 17px; color: var(--white); letter-spacing: .3px;
  }
  .product-name {
    position: absolute; top: 300px; left: 88px;
    font-family: "Oswald", sans-serif; font-weight: 700;
    font-size: 66px; line-height: 1; color: var(--white); letter-spacing: 1px;
  }
  .product-name--tail { left: 386px; }
  .oil-drop {
    position: absolute; left: 309px; top: 242px; width: 76px; height: 108px;
    border-radius: 50% 50% 50% 50% / 62% 62% 38% 38%;
    background: radial-gradient(circle at 45% 62%, var(--gold-light), #e0a625 45%, var(--gold-deep) 85%);
  }
  .tagline {
    position: absolute; left: 88px; top: 382px;
    font-family: "Montserrat", sans-serif; font-weight: 500;
    font-size: 18.5px; color: var(--white); letter-spacing: .4px;
  }

  .benefit {
    position: absolute; left: 42px; top: 512px;
    color: var(--cream-text);
  }
  .benefit__title {
    font-family: "Oswald", sans-serif; font-weight: 600;
    font-size: 25px; line-height: 1.15; letter-spacing: .3px; color: var(--white);
  }
  .benefit__line { font-family: "Roboto", sans-serif; font-size: 19px; line-height: 23px; }

  .fruit-art {
    position: absolute; left: 274px; top: 474px; width: 184px; height: 142px;
    border-radius: 48% 52% 45% 55%;
    background: radial-gradient(circle at 40% 40%, #d8644a, var(--fruit-red) 50%, var(--fruit-dark) 100%);
  }
  .badge-mark {
    position: absolute; left: 49px; top: 602px; width: 28px; height: 28px;
    border-radius: 50%; background: var(--label-black);
  }
  .volume {
    position: absolute; left: 232px; top: 636px; width: 220px;
    text-align: center;
    font-family: "Oswald", sans-serif; font-weight: 600;
    font-size: 23px; color: var(--dark-text); letter-spacing: .2px;
  }
</style>
</head>
<body>
  <main class="label">
    <svg class="label__shapes" viewBox="0 0 527 712" width="527" height="712" aria-hidden="true">
      <path d="M0 440 C 40 432 80 426 97 426 L 103 418 L 109 426 C 210 428 300 460 380 486 C 440 504 490 500 527 486 L 527 672 L 0 672 Z" fill="var(--brick-light)"/>
      <path d="M0 470 C 90 452 210 462 320 500 C 410 530 470 540 527 520 L 527 672 L 0 672 Z" fill="var(--brick)"/>
      <rect x="0" y="668" width="527" height="10" fill="var(--olive)"/>
      <path d="M244 632 L 440 632 L 452 672 L 232 672 Z" fill="var(--olive)"/>
    </svg>

    <div class="brand-plate">
      <span class="brand-plate__name">MEADOWLARK</span>
      <span class="brand-plate__sub">SCALP PARLOUR</span>
    </div>

    <p class="claim">100% PURE &amp; NATURAL</p>
    <h1 class="product-name">JOJOBA</h1>
    <div class="oil-drop" role="img" aria-label="Golden oil drop standing in for the letter O"></div>
    <span class="product-name product-name--tail" aria-hidden="true">IL</span>
    <p class="tagline">REAL INGREDIENTS. REAL RESULTS.</p>

    <div class="benefit">
      <p class="benefit__title">COLD-PRESSED OIL</p>
      <p class="benefit__line">for skin hair &amp; body</p>
      <p class="benefit__line">multi-purpose Anti-aging</p>
    </div>

    <div class="fruit-art" role="img" aria-label="Illustration of ripe jojoba fruits with green leaves"></div>
    <div class="badge-mark" role="img" aria-label="Non-GMO badge"></div>

    <p class="volume">4fl. oz (118 ml)</p>
  </main>
</body>
</html>
```